Blog Banner Design Project: Wanderly Ledger

Looking for a new banner for my blog " Neville Ostrander's Wanderly Ledger" at http://www.wanderlyledger.net - and once design agreed also want an updated album art for the podcast that goes along with the site.
For more about the blog and what it is about:
http://www.wanderlyledger.net/about
Wanderly Ledger is a Luxury Travel Blog And Podcast that provides inspiration, advice and tips about luxurious travel experiences, including destinations, transportation, accommodation, and journeys, that travellers can read, listen to or watch.
Objective of the new design
(1) retain the colour scheme ideally to retain the brand identity, as have been using these colours since 2005.
(2) introduce more of my personality and make it more visually and overt that it is "Neville Ostrander's Wanderly Ledger", so possibly introducing my image into the blog banner so visitors are clear and more aware of the person behind the brand.
(3) needs to have an up-market, luxury but modern feel.
(4) if possible reflect the focus on the content (destinations, transportation, accommodation, attractions and journeys) - but this maybe best left to just words as want the design to be bold and more of the branding and personality.
Ideal wording
Smallish: Neville Ostrander's
Main wording: Wanderly Ledger
Sub-title/ small: luxurious destinations, transportation, accommodation and journeys.
I have a poll running with readers of my blog to rate the designs to help me to chose the final route, and so there is no need to submit any more designs. I will make the decision once the poll closes on the weekend.

```html
<!DOCTYPE html>
<html lang="en">
<head>
<meta charset="utf-8">
<title>Neville Ostrander's Wanderly Ledger – Blog Banner</title>
<link rel="stylesheet" href="https://fonts.googleapis.com/css2?family=Satisfy&family=Fanwood+Text&family=Crimson+Text:wght@700&display=swap">
<style>
  :root {
    --dusk-purple: #4f4270;
    --lilac: #8f82ad;
    --haze: #b49bb0;
    --sunset-orange: #f2a43a;
    --sun-gold: #ffc95a;
    --magenta: #a8288f;
    --ink: #111014;
    --white: #ffffff;
  }
  * { margin: 0; padding: 0; box-sizing: border-box; }
  html, body { width: 1200px; height: 202px; overflow: hidden; background: var(--white); }
  .banner {
    position: relative;
    width: 1200px;
    height: 202px;
    overflow: hidden;
  }
  .banner__scene {
    position: absolute;
    inset: 0;
    background:
      radial-gradient(ellipse 260px 160px at 1080px 120px, var(--sun-gold) 0%, rgba(242,164,58,0.6) 45%, rgba(242,164,58,0) 100%),
      linear-gradient(90deg, var(--dusk-purple) 0%, #6c5d8e 25%, var(--lilac) 50%, var(--haze) 68%, #d99a6a 82%, var(--sunset-orange) 100%);
  }
  .banner__portrait {
    position: absolute;
    left: 0;
    top: 0;
    width: 300px;
    height: 202px;
    background: linear-gradient(180deg, rgba(60,50,80,0) 0%, rgba(70,64,90,0.5) 55%, rgba(40,44,60,0.8) 100%);
  }
  .banner__byline {
    position: absolute;
    left: 271px;
    top: 19px;
    width: 286px;
    height: 48px;
    background: var(--magenta);
    clip-path: polygon(0 0, 100% 0, 95% 100%, 0 100%);
    color: var(--white);
    font-family: "Satisfy", cursive;
    font-size: 32px;
    line-height: 48px;
    padding-left: 18px;
    white-space: nowrap;
  }
  .banner__title-band {
    position: absolute;
    left: 342px;
    top: 66px;
    width: 645px;
    height: 86px;
    background: linear-gradient(90deg, rgba(17,16,20,0.94) 0%, rgba(17,16,20,0.88) 70%, rgba(17,16,20,0.75) 100%);
    clip-path: polygon(6% 0, 100% 0, 95% 100%, 0 100%);
  }
  .banner__title {
    position: absolute;
    left: 382px;
    top: 66px;
    color: var(--white);
    font-family: "Fanwood Text", serif;
    font-weight: 400;
    font-size: 74px;
    line-height: 86px;
    white-space: nowrap;
  }
  .banner__tagline {
    position: absolute;
    left: 417px;
    top: 161px;
    width: 783px;
    height: 37px;
    background: rgba(17,16,20,0.94);
    clip-path: polygon(1.5% 0, 100% 0, 100% 100%, 0 100%);
    color: var(--white);
    font-family: "Crimson Text", serif;
    font-weight: 700;
    font-size: 19.5px;
    line-height: 37px;
    padding-left: 14px;
    white-space: nowrap;
  }
</style>
</head>
<body>
  <header class="banner">
    <div class="banner__scene" role="img" aria-label="Tropical beach with palm trees at sunset, purple sky fading to an orange sun over the sea"></div>
    <div class="banner__portrait" role="img" aria-label="Portrait of Neville Ostrander smiling, wearing a dark hoodie"></div>
    <p class="banner__byline">Neville Ostrander's</p>
    <div class="banner__title-band"></div>
    <h1 class="banner__title">Wanderly Ledger</h1>
    <p class="banner__tagline">Luxurious destinations, transportation, accommodation and journeys.</p>
  </header>
</body>
</html>
```